New Business Card Design Project

Need a design that will create an impact / strong impression towards our clients for our business. We are in the lighting business and we do lighting retrofits for large commercial to industrial clientele.

Target Market(s)

Lighting Industry

Industry/Entity Type

Business

Font styles to use
Other font styles liked:
• we would like to use the font on our logo, not sure what it is though..

Requirements
Must have
• Our logo.
Nice to have
• We are open to suggestions that have to do with lighting.

```html
<!DOCTYPE html>
<html lang="en">
<head>
<meta charset="utf-8">
<title>Northline Relight Co. — Business Card</title>
<link href="https://fonts.googleapis.com/css2?family=Montserrat:wght@400;500;600;700&display=swap" rel="stylesheet">
<style>
  :root {
    --backdrop: #2a2a2a;
    --paper: #ffffff;
    --green-deep: #133d14;
    --green-brand: #0b8a3a;
    --green-dark-text: #1a4a1c;
    --text-grey: #555555;
    --rule-grey: #c9c9c9;
  }
  * { margin: 0; padding: 0; box-sizing: border-box; }
  html, body {
    width: 1200px; height: 960px; overflow: hidden;
    background: var(--backdrop);
    font-family: "Montserrat", sans-serif;
  }
  .stage { position: relative; width: 1200px; height: 960px; }

  .card {
    position: absolute;
    width: 600px; height: 343px;
    box-shadow: 0 3px 8px rgba(0,0,0,0.45);
    overflow: hidden;
  }
  .card--front { left: 314px; top: 113px; background: var(--paper); }
  .card--back  { left: 311px; top: 472px; background: var(--green-deep); }

  /* wordmark */
  .wordmark {
    position: absolute;
    display: flex; align-items: center; gap: 8px;
    font-weight: 700; letter-spacing: 0.3px; white-space: nowrap;
  }
  .wordmark__square { width: 13px; height: 13px; flex: none; }
  .card--front .wordmark { left: 44px; top: 160px; font-size: 16px; color: var(--green-deep); }
  .card--front .wordmark__square { background: var(--green-brand); }
  .card--back .wordmark {
    left: 0; right: 0; top: 152px; justify-content: center;
    font-size: 28px; color: #ffffff;
  }
  .card--back .wordmark__square { width: 20px; height: 20px; background: #ffffff; }

  .divider {
    position: absolute; left: 320px; top: 85px;
    width: 1px; height: 183px; background: var(--rule-grey);
  }

  .contact { position: absolute; left: 345px; top: 86px; }
  .contact__name {
    font-size: 19px; font-weight: 700; color: var(--green-dark-text); line-height: 22px;
  }
  .contact__title {
    font-size: 16px; font-weight: 500; color: var(--green-brand); line-height: 20px;
    margin-bottom: 8px;
  }
  .contact__address {
    font-size: 15px; color: var(--text-grey); line-height: 19px; margin-bottom: 5px;
    font-style: normal;
  }
  .contact__list { list-style: none; }
  .contact__item {
    display: flex; align-items: center; gap: 9px;
    font-size: 15px; color: var(--text-grey); line-height: 19px;
  }
  .contact__icon { width: 13px; height: 13px; flex: none; fill: var(--green-dark-text); }

  .web-band { position: absolute; left: 0; top: 299px; width: 570px; height: 31px; }
  .web-band__shape { position: absolute; inset: 0; }
  .web-band__url {
    position: absolute; left: 0; width: 540px; top: 0; line-height: 31px;
    text-align: center; color: #ffffff; font-size: 12px; font-weight: 600;
    letter-spacing: 3.2px; text-transform: uppercase;
  }
</style>
</head>
<body>
<main class="stage">

  <section class="card card--front" aria-label="Business card front">
    <div class="wordmark"><span class="wordmark__square"></span>NORTHLINE RELIGHT CO.</div>

    <div class="divider"></div>

    <div class="contact">
      <p class="contact__name">JORDAN HALE</p>
      <p class="contact__title">CEO/FOUNDER</p>
      <address class="contact__address">4210 Birchwood Court<br>Fairview, Oregon 97024</address>
      <ul class="contact__list">
        <li class="contact__item">
          <svg class="contact__icon" viewBox="0 0 16 16" aria-hidden="true"><path d="M1 5c0-2 3-3 7-3s7 1 7 3v1h-4V5H5v1H1z"/><rect x="3" y="7" width="10" height="7" rx="1"/></svg>
          555 201 4873
        </li>
        <li class="contact__item">
          <svg class="contact__icon" viewBox="0 0 16 16" aria-hidden="true"><path d="M4 1h8v14H4z M5.5 3v9h5V3z"/></svg>
          555 318 6092
        </li>
        <li class="contact__item">
          <svg class="contact__icon" viewBox="0 0 16 16" aria-hidden="true"><rect x="4" y="1" width="8" height="5"/><rect x="1" y="7" width="14" height="7" rx="1"/></svg>
          555 427 3159
        </li>
        <li class="contact__item">
          <svg class="contact__icon" viewBox="0 0 16 16" aria-hidden="true"><path d="M1 4h14v9H1z"/><path d="M1 4l7 5 7-5" fill="none" stroke="#fff" stroke-width="1.3"/></svg>
          name@northlinerelight.com
        </li>
      </ul>
    </div>

    <div class="web-band">
      <svg class="web-band__shape" viewBox="0 0 570 31" preserveAspectRatio="none" aria-hidden="true">
        <polygon points="0,0 540,0 570,31 0,31" fill="var(--green-brand)"/>
      </svg>
      <p class="web-band__url">www.northlinerelight.com</p>
    </div>
  </section>

  <section class="card card--back" aria-label="Business card back">
    <div class="wordmark"><span class="wordmark__square"></span>NORTHLINE RELIGHT CO.</div>
  </section>

</main>
</body>
</html>
```